Marla’s Sandwich Corner Grand Opening Door Flyer

1. Project Title
• “Flyer Design for Sandwich Shop Grand Opening”
• Why it’s effective: Direct and to the point, highlighting the purpose of the design.

2. Project Description
• “We’re looking for a professional designer to create a vibrant and modern flyer for our sandwich shop, Marla’s Corner. The flyer should emphasize our handcrafted sandwiches, fresh-baked bread, and house-made meats. As a women & family-owned business, we want this aspect prominently displayed. The flyer should also include our logo, a ‘Grand Opening’ and our website: MarlasCorner.example. We want the design to be clean, bold, and visually appealing to attract customers. We also would like a QR code so they can scan to load of the website to order online, but also list it.
• Why it’s effective: Clear goals, modern style preference, and necessary details outlined.

3. Visual Style
• “Modern, bold, and clean design with bright, appetizing colors. Focus on high-quality imagery of sandwiches, sleek fonts, and an inviting layout.”
• Why it’s effective: Communicates the desired aesthetic and tone.

4. Key Details to Include
• Business Name: Marla’s Sandwich Corner
• Taglines:
“Women & Family Owned”
“Handcrafted Sandwiches Made with Love”
“Fresh Baked Bread”
“House-made Slow Roasted House Specialties”
“Gluten-Friendly”
“Vegan-Friendly”
“7:00am Fresh Daily Grounded Coffee and Breakfast”

• Call-to-Action: “Order Online at MarlasCorner.example”
• Placeholder for the logo.
• Size: 4.25 x 11 (Door Hanger)
• File Format: High-resolution PDF, JPEG, or PNG.
• Print-Ready: Include bleed margins and ensure print clarity.

6. Tone
• Friendly and professional. Highlighting that your business is women-owned adds a unique and personal touch vs deli meat shops. We are a gourmet sandwich shop, with fresh baked bread, house-made meats, with gluten and vegan options. Each sandwich is made with love.

Target Market(s)

Coffee drinkers for morning crowd and sandwiches for lunch

Industry/Entity Type

Sandwich Shop

Colors
EB3D1F
EC4F4E
F09395
F8D3D4
FCEDEE

Requirements
Must have
• See Description
Nice to have
• Use website to get a feel for color theme
Should not have
• NA

```html
<!DOCTYPE html>
<html lang="en">
<head>
<meta charset="utf-8">
<title>Marla’s Sandwich Corner – Grand Opening Door Hanger</title>
<link rel="stylesheet" href="https://fonts.googleapis.com/css2?family=Fraunces:wght@900&family=Archivo+Black&family=Montserrat:wght@800&display=swap">
<style>
  :root {
    --tomato: #EB3D1F;
    --tomato-bright: #EF5A33;
    --rose: #F09395;
    --blush: #F5C0D9;
    --blush-light: #F8D3D4;
    --cream: #FCEDEE;
    --white: #FFFFFF;
  }
  * { margin: 0; padding: 0; box-sizing: border-box; }
  html, body { width: 1200px; height: 3300px; overflow: hidden; background: var(--tomato); }
  .flyer { position: relative; width: 1200px; height: 3300px; overflow: hidden; background: var(--tomato); }
  .pattern-field { position: absolute; inset: 0; background: linear-gradient(180deg, var(--tomato-bright) 0%, var(--tomato) 100%); }
  .layer { position: absolute; left: 0; top: 0; width: 1200px; height: 3300px; }
  .food-photo {
    position: absolute; left: 314px; top: 1499px; width: 653px; height: 519px;
    border-radius: 46% 46% 40% 40%;
    background: radial-gradient(ellipse at 50% 55%, #F3E6D2 0%, #E7C9A0 35%, #F7D6E2 75%, rgba(248,211,212,0) 100%);
  }
  .features {
    position: absolute; left: 0; top: 2088px; width: 1200px;
    text-align: center; color: var(--tomato);
    font-family: "Archivo Black", sans-serif; text-transform: uppercase;
    font-size: 37px; line-height: 34px; letter-spacing: 1px;
  }
  .features li { list-style: none; margin-bottom: 25px; }
  .features li:nth-child(7) { margin-top: 6px; }
  .cta-pill {
    position: absolute; left: 199px; top: 2770px; width: 798px; height: 103px;
    border-radius: 34px; background: var(--blush);
    color: var(--tomato); font-family: "Montserrat", sans-serif; font-weight: 800;
    font-size: 82px; line-height: 103px; text-align: center; letter-spacing: -1px;
  }
  .cta-url {
    position: absolute; left: 0; top: 2878px; width: 1200px; text-align: center;
    color: var(--blush); font-family: "Fraunces", serif; font-weight: 900;
    font-size: 86px; line-height: 110px; letter-spacing: -2px;
  }
  .footer-art {
    position: absolute; left: 318px; top: 3072px; width: 528px; height: 112px;
    border-radius: 56px;
    background: linear-gradient(180deg, #F7CCDF 0%, #F3B5CF 100%);
  }
  .motto {
    position: absolute; left: 0; top: 3200px; width: 1200px; text-align: center;
    color: var(--tomato); font-family: "Montserrat", sans-serif; font-weight: 800;
    font-size: 28px; letter-spacing: 5px;
  }
</style>
</head>
<body>
<main class="flyer">
  <div class="pattern-field" role="img" aria-label="Repeating pattern of outline motifs on orange"></div>

  <svg class="layer" viewBox="0 0 1200 3300" aria-hidden="true">
    <defs>
      <linearGradient id="oval-fill" x1="0" y1="0" x2="0" y2="1">
        <stop offset="0" stop-color="#F4BCD6"/>
        <stop offset="0.55" stop-color="#F7D3E3"/>
        <stop offset="0.75" stop-color="#FFFFFF"/>
        <stop offset="1" stop-color="#FFFFFF"/>
      </linearGradient>
      <linearGradient id="footer-fill" x1="0" y1="0" x2="0" y2="1">
        <stop offset="0" stop-color="#FCE4EE"/>
        <stop offset="0.3" stop-color="#F6C4DB"/>
        <stop offset="1" stop-color="#F5C0D9"/>
      </linearGradient>
    </defs>
    <ellipse class="hero-oval" cx="600" cy="1710" rx="1080" ry="1018" fill="url(#oval-fill)"/>
    <path class="footer-band" d="M0 3062 Q600 2960 1200 3062 L1200 3300 L0 3300 Z" fill="url(#footer-fill)"/>

    <path class="headline-frame" d="M141 1121 L141 950 Q141 903 188 903 L231 903 L231 840 Q231 794 277 794 L934 794 Q980 794 980 840 L980 903 L1016 903 Q1063 903 1063 950 L1063 1121"
          fill="none" stroke="var(--tomato)" stroke-width="6" stroke-linejoin="round"/>
    <line x1="141" y1="1121" x2="1063" y2="1121" stroke="var(--tomato)" stroke-width="6"/>

    <g fill="var(--tomato)" font-family="Fraunces, serif" font-weight="900">
      <text class="headline" x="276" y="968" font-size="190" textLength="640" lengthAdjust="spacingAndGlyphs">Grand</text>
      <text class="headline" x="172" y="1088" font-size="190" textLength="848" lengthAdjust="spacingAndGlyphs">Opening</text>
      <text class="brand-name" x="147" y="1418" font-size="250" textLength="908" lengthAdjust="spacingAndGlyphs">Marla’s</text>
    </g>
    <text class="brand-sub" x="212" y="1494" font-size="66" font-family="Archivo Black, sans-serif" fill="var(--tomato)" textLength="773" lengthAdjust="spacingAndGlyphs">SANDWICH CORNER</text>

    <line x1="493" y1="2059" x2="698" y2="2059" stroke="var(--tomato)" stroke-width="4" stroke-linecap="round"/>
    <line x1="493" y1="2620" x2="698" y2="2620" stroke="var(--tomato)" stroke-width="4" stroke-linecap="round"/>
  </svg>

  <div class="food-photo" role="img" aria-label="Photo of a fresh sandwich with lettuce, tomato and peppers beside a cup of coffee, with a small round sticker"></div>

  <ul class="features">
    <li>• Women &amp; Family Owned •</li>
    <li>• Handcrafted Sandwiches •<br>Made With Love</li>
    <li>• Fresh Baked Bread •</li>
    <li>• House-Made Slow Roasted •<br>House Specialties</li>
    <li>• Gluten-Friendly •</li>
    <li>• Vegan-Friendly •</li>
    <li>• 7:00AM Fresh Daily •<br>Grounded Coffee and Breakfast</li>
  </ul>

  <div class="cta-pill">ORDER ONLINE AT</div>
  <div class="cta-url">MarlasCorner.example</div>

  <div class="footer-art" role="img" aria-label="Row of three small line illustrations for peace, love and sandwiches"></div>
  <p class="motto">PEACE ✦ LOVE ✦ SANDWICHES</p>
</main>
</body>
</html>
```